Business Card Design for RB Wine:

I'm looking for a card that has the following.
Front:
- Merlot Colored
- stripe down the middle in silver or gold flake
- RB in block like thick letters with gold or silver flake above stripe
-Wine: below stripe
- a grape bunch that is at the end of the stripe that is made so it can be printed as embossed
Back:
- line down the middle of card in Merlot, card is white background
- to the left Marisa Dutton, (next line) Owner, (next line) Certified Sommelier, GVA
- to the right (listed) restaurant consulting, wine tours, personal tastings, event planning, personal wine buying
- add embossed grape bunch
Also, looking for a piece that slides over like a envelope for a room key for a hotel that says "We met @ PALVIN" and possibly a file for that, that I can edit.
Would like card to be printed on a thicker cardstock

```html
<!DOCTYPE html>
<html lang="en">
<head>
<meta charset="utf-8">
<title>RB Wine – Business Card</title>
<link rel="stylesheet" href="https://fonts.googleapis.com/css2?family=Open+Sans:wght@400;600&display=swap">
<style>
  :root {
    --merlot: #6a0011;
    --merlot-light: #7f1a2a;
    --gold: #dcaa2a;
    --gold-deep: #c9951c;
    --card-white: #f1f1f1;
    --grape-grey: #d9d9d9;
    --ink: #1c1c1c;
    --stage: #e8e6e3;
  }
  * { margin: 0; padding: 0; box-sizing: border-box; }
  html, body {
    width: 1200px;
    height: 900px;
    overflow: hidden;
    background: var(--stage);
  }
  .canvas {
    position: relative;
    width: 1200px;
    height: 900px;
  }

  /* Front of card */
  .card-front {
    position: absolute;
    left: 135px;
    top: 55px;
    width: 588px;
    height: 365px;
    background: var(--merlot);
    overflow: hidden;
  }
  .card-front__name {
    position: absolute;
    left: 70px;
    top: 150px;
    font-family: "Open Sans", sans-serif;
    font-weight: 600;
    font-size: 48px;
    line-height: 1;
    white-space: nowrap;
    color: var(--gold);
  }
  .card-front__grapes {
    position: absolute;
    left: 320px;
    top: 45px;
    width: 268px;
    height: 255px;
  }
  .card-front__stripe {
    position: absolute;
    left: 0;
    top: 300px;
    width: 100%;
    height: 37px;
    background: linear-gradient(180deg, var(--gold) 0%, var(--gold-deep) 100%);
  }

  /* Back of card */
  .card-back {
    position: absolute;
    left: 388px;
    top: 455px;
    width: 567px;
    height: 351px;
    background: var(--card-white);
    overflow: hidden;
  }
  .card-back__divider {
    position: absolute;
    left: 247px;
    top: 0;
    width: 3px;
    height: 100%;
    background: var(--merlot);
  }
  .card-back__grapes {
    position: absolute;
    left: 307px;
    top: 95px;
    width: 255px;
    height: 240px;
  }
  .contact {
    position: absolute;
    left: 41px;
    top: 137px;
    font-family: "Open Sans", sans-serif;
    color: var(--ink);
  }
  .contact__name {
    font-size: 20px;
    font-weight: 600;
    color: var(--merlot);
    text-transform: uppercase;
    line-height: 26px;
  }
  .contact__role {
    font-size: 14px;
    line-height: 22px;
  }
  .contact__credential {
    margin-top: 9px;
    font-size: 14px;
    line-height: 20px;
  }
  .services {
    position: absolute;
    left: 277px;
    top: 126px;
    list-style: none;
    font-family: "Open Sans", sans-serif;
    font-size: 15px;
    line-height: 20.5px;
    color: var(--ink);
  }
  .services li {
    position: relative;
    padding-left: 15px;
  }
  .services li::before {
    content: "";
    position: absolute;
    left: 0;
    top: 6px;
    width: 8px;
    height: 8px;
    border-radius: 50%;
    background: var(--merlot);
  }
</style>
</head>
<body>
<main class="canvas">

  <section class="card-front" aria-label="Card front">
    <svg class="card-front__grapes" role="img" aria-label="Embossed grape bunch illustration" viewBox="0 0 268 255">
      <defs>
        <radialGradient id="grapeFrontTone" cx="40%" cy="55%" r="60%">
          <stop offset="0%" stop-color="#7f1a2a" stop-opacity="0.9"/>
          <stop offset="100%" stop-color="#7f1a2a" stop-opacity="0.35"/>
        </radialGradient>
      </defs>
      <path d="M10 60 Q140 40 268 60 L268 170 Q200 255 80 255 Q10 200 10 60 Z" fill="url(#grapeFrontTone)"/>
    </svg>
    <p class="card-front__name">RB Wine</p>
    <div class="card-front__stripe"></div>
  </section>

  <section class="card-back" aria-label="Card back">
    <svg class="card-back__grapes" role="img" aria-label="Embossed grape bunch illustration" viewBox="0 0 255 240">
      <defs>
        <radialGradient id="grapeBackTone" cx="40%" cy="55%" r="60%">
          <stop offset="0%" stop-color="#d9d9d9"/>
          <stop offset="100%" stop-color="#d9d9d9" stop-opacity="0.4"/>
        </radialGradient>
      </defs>
      <path d="M10 50 Q130 25 255 50 L255 140 Q190 240 70 240 Q5 185 10 50 Z" fill="url(#grapeBackTone)"/>
    </svg>
    <div class="card-back__divider"></div>

    <div class="contact">
      <p class="contact__name">Marisa Dutton</p>
      <p class="contact__role">Owner</p>
      <p class="contact__credential">Certified Sommelier, GVA</p>
    </div>

    <ul class="services">
      <li>Restaurant Consulting</li>
      <li>Wine Tours</li>
      <li>Personal Tastings</li>
      <li>Event Planning</li>
      <li>Personal wine buying</li>
    </ul>
  </section>

</main>
</body>
</html>
```